Business Card for a Dental Office

The design should communicate integrity, quality and reliability. We also want the card look elegant, simple, but still stand out, different from the traditional-dental-office business card.

Industry/Entity Type

Business

```html
<!DOCTYPE html>
<html lang="en">
<head>
<meta charset="utf-8">
<title>Harwell Dental Studio – Business Card</title>
<link rel="stylesheet" href="https://fonts.googleapis.com/css2?family=Oswald:wght@500&family=Open+Sans:wght@400;600&display=swap">
<style>
  :root {
    --ink: #141414;
    --paper: #ffffff;
    --gold: #e2cc1c;
    --gold-deep: #b89a10;
    --grey: #6a6a6a;
    --stage: #e9e7e2;
  }
  * { margin: 0; padding: 0; box-sizing: border-box; }
  html, body { width: 1200px; height: 843px; overflow: hidden; }
  body {
    background: var(--stage);
    font-family: "Open Sans", Arial, sans-serif;
    display: flex; align-items: center; justify-content: center; gap: 40px;
  }
  .card {
    position: relative; width: 540px; height: 310px; overflow: hidden;
    box-shadow: 0 6px 18px rgba(0,0,0,.18);
  }

  /* Back side */
  .card-back { background: var(--ink); color: var(--paper); }
  .card-back .brand {
    position: absolute; left: 40px; top: 110px;
    display: flex; align-items: center; gap: 18px;
  }
  .card-back .brand-square { width: 64px; height: 64px; background: var(--gold); }
  .card-back .brand-name {
    font-family: "Oswald", Arial, sans-serif; font-weight: 500;
    font-size: 34px; color: var(--gold); letter-spacing: .5px; line-height: 1;
  }
  .card-back .tagline {
    position: absolute; left: 122px; top: 166px;
    font-size: 11px; font-weight: 600; letter-spacing: 1px; text-transform: uppercase; color: var(--paper);
  }
  .card-back .web {
    position: absolute; left: 122px; top: 186px;
    font-size: 12px; letter-spacing: 2px; color: var(--gold);
  }

  /* Front side */
  .card-front { background: var(--paper); color: var(--ink); }
  .card-front .brand { position: absolute; left: 170px; top: 38px; }
  .card-front .brand-name {
    font-family: "Oswald", Arial, sans-serif; font-weight: 500;
    font-size: 27px; text-transform: uppercase; letter-spacing: .3px; line-height: 1;
  }
  .card-front .tagline {
    margin-top: 4px; font-size: 10px; font-weight: 600; letter-spacing: .9px;
    text-transform: uppercase; color: var(--gold-deep);
  }
  .person {
    position: absolute; right: 300px; top: 118px; text-align: right; white-space: nowrap;
  }
  .person .name { font-size: 17px; font-weight: 600; }
  .person .role { font-size: 12px; color: var(--gold-deep); margin-bottom: 4px; }
  .person .address { font-size: 11.5px; color: var(--grey); line-height: 1.45; }
  .divider {
    position: absolute; left: 254px; top: 122px; width: 1px; height: 78px; background: #cfcfcf;
  }
  .contacts { position: absolute; left: 270px; top: 120px; list-style: none; }
  .contacts li {
    display: flex; align-items: center; gap: 8px;
    font-size: 12px; color: var(--grey); height: 19px;
  }
  .contacts svg { width: 12px; height: 12px; fill: var(--ink); flex: none; }

  .band-line {
    position: absolute; left: 0; bottom: 54px; width: 330px; height: 4px; background: var(--gold);
  }
  .band-dark {
    position: absolute; left: 0; bottom: 20px; width: 330px; height: 30px; background: var(--ink);
    color: var(--paper); font-size: 12px; letter-spacing: 2.5px;
    display: flex; align-items: center; padding-left: 40px;
  }
  .band-gold {
    position: absolute; right: 0; bottom: 20px; width: 150px; height: 30px;
    background: linear-gradient(90deg, var(--paper), var(--gold) 60%);
  }
  .band-square {
    position: absolute; right: 112px; bottom: 24px; width: 22px; height: 22px; background: var(--ink);
  }
</style>
</head>
<body>

  <section class="card card-back" aria-label="Card back">
    <div class="brand">
      <span class="brand-square"></span>
      <span class="brand-name">HARWELL DENTAL STUDIO</span>
    </div>
    <p class="tagline">Your smile is your gift to others</p>
    <p class="web">www.harwelldental.com</p>
  </section>

  <section class="card card-front" aria-label="Card front">
    <div class="brand">
      <p class="brand-name">Harwell Dental Studio</p>
      <p class="tagline">Your smile is your gift to others</p>
    </div>

    <div class="person">
      <p class="name">Daniel Reyes</p>
      <p class="role">CEO/Founder</p>
      <p class="address">2140 Cedar Hollow Road<br>Juneau, Alaska 99801</p>
    </div>

    <span class="divider"></span>

    <ul class="contacts">
      <li><svg viewBox="0 0 24 24"><path d="M6.6 10.8a15 15 0 0 0 6.6 6.6l2.2-2.2c.3-.3.7-.4 1-.2 1.1.4 2.3.6 3.6.6.6 0 1 .4 1 1V20c0 .6-.4 1-1 1A17 17 0 0 1 3 4c0-.6.4-1 1-1h3.5c.6 0 1 .4 1 1 0 1.3.2 2.5.6 3.6.1.3 0 .7-.2 1z"/></svg>555 210 4471</li>
      <li><svg viewBox="0 0 24 24"><path d="M7 1h10a2 2 0 0 1 2 2v18a2 2 0 0 1-2 2H7a2 2 0 0 1-2-2V3a2 2 0 0 1 2-2zm0 3v14h10V4zm5 15.5a1 1 0 1 0 0 2 1 1 0 0 0 0-2z"/></svg>555 318 6620</li>
      <li><svg viewBox="0 0 24 24"><path d="M6 2h12v5H6zM3 8h18a1 1 0 0 1 1 1v8h-4v5H6v-5H2V9a1 1 0 0 1 1-1zm5 8v4h8v-4z"/></svg>555 742 0193</li>
      <li><svg viewBox="0 0 24 24"><path d="M2 5h20v14H2zm2 2v.5l8 5 8-5V7zm0 2.9V17h16V9.9l-8 5z"/></svg>hello@harwelldental.com</li>
    </ul>

    <span class="band-line"></span>
    <div class="band-dark">www.harwelldental.com</div>
    <span class="band-gold"></span>
    <span class="band-square"></span>
  </section>

</body>
</html>
```